Book Cover

Hello!
I need someone to design a book cover with the title, subtitle and one of the photos attached.

- Title: Walking Past Winter - By Corwin Haskett
- Subtitle: A Practical Path to living a calm and joyful life after treatment.

```html
<!DOCTYPE html>
<html lang="en">
<head>
<meta charset="utf-8">
<title>Walking Past Winter — Book Cover</title>
<link rel="stylesheet" href="https://fonts.googleapis.com/css2?family=Oswald:wght@400;700&family=Archivo:wght@500&display=swap">
<style>
  :root {
    --stage: #e9e6e8;
    --paper: #f7f7f5;
    --ink: #1d2233;
    --navy: #1f2f63;
    --blue: #5f7fc9;
    --sky: #9fb6df;
    --bark: #6b5a44;
  }
  html, body {
    margin: 0;
    width: 1200px;
    height: 923px;
    overflow: hidden;
    background: var(--stage);
  }
  .cover {
    position: absolute;
    left: 343px;
    top: 31px;
    width: 514px;
    height: 860px;
    background: var(--paper);
    overflow: hidden;
    box-shadow: 0 2px 10px rgba(0,0,0,0.12);
  }
  .cover-photo {
    position: absolute;
    left: 0;
    top: 0;
    width: 252px;
    height: 100%;
    background:
      radial-gradient(ellipse 70% 30% at 60% 32%, rgba(210,170,140,0.55), transparent 70%),
      linear-gradient(180deg, var(--sky) 0%, var(--bark) 35%, #4a4d63 58%, var(--navy) 100%);
  }
  .title {
    position: absolute;
    left: 250px;
    top: 96px;
    height: 592px;
    margin: 0;
    writing-mode: vertical-rl;
    transform: rotate(180deg);
    font-family: "Oswald", sans-serif;
    font-weight: 700;
    font-size: 100px;
    line-height: 0.96;
    letter-spacing: -1px;
    text-transform: uppercase;
    white-space: nowrap;
    background: linear-gradient(90deg, var(--navy) 0%, var(--blue) 55%, var(--sky) 100%);
    -webkit-background-clip: text;
    background-clip: text;
    color: transparent;
  }
  .subtitle {
    position: absolute;
    left: 352px;
    top: 698px;
    width: 140px;
    margin: 0;
    font-family: "Archivo", sans-serif;
    font-weight: 500;
    font-size: 8.5px;
    line-height: 1.25;
    letter-spacing: 0.4px;
    text-transform: uppercase;
    color: var(--ink);
  }
  .byline {
    position: absolute;
    left: 352px;
    top: 748px;
    margin: 0;
    font-family: "Oswald", sans-serif;
    color: var(--ink);
    text-transform: uppercase;
  }
  .byline-label {
    display: block;
    font-family: "Archivo", sans-serif;
    font-size: 8.5px;
    margin-bottom: 4px;
  }
  .author {
    display: block;
    font-weight: 400;
    font-size: 30px;
    line-height: 1;
    letter-spacing: 0.5px;
  }
</style>
</head>
<body>
  <main class="cover">
    <div class="cover-photo" role="img" aria-label="Photo of an older man outdoors looking up toward the sky, wearing a blue shirt and vest"></div>
    <h1 class="title">Walking<br>Past Winter</h1>
    <p class="subtitle">A Practical Path to living a calm and joyful life after treatment.</p>
    <p class="byline">
      <span class="byline-label">By</span>
      <span class="author">Corwin<br>Haskett</span>
    </p>
  </main>
</body>
</html>
```